Dunmore Roofing

Want a professional looking business card

Industry/Entity Type

Business

Contact Information for Business Card

Paul Dunmore ( Owner) paul@dunmoreroofing-example.com, www.dunmoreroofing-example.com, Adress: 4172 Township road 43 Ashcombe,WR K9X4T2

```html
<!DOCTYPE html>
<html lang="en">
<head>
<meta charset="utf-8">
<title>Dunmore Roofing – Business Card</title>
<link rel="stylesheet" href="https://fonts.googleapis.com/css2?family=Roboto:wght@400;500;700&display=swap">
<style>
  :root {
    --brand-blue: #1b4a8d;
    --brand-blue-light: #2a5aa0;
    --brand-grey: #8a8a8a;
    --text-grey: #6b6b6b;
    --card-white: #ffffff;
    --page-bg: #d9d9d9;
  }
  * { margin: 0; padding: 0; box-sizing: border-box; }
  html, body {
    width: 1200px; height: 1000px; overflow: hidden;
    background: var(--page-bg);
    font-family: "Roboto", Arial, sans-serif;
  }
  .canvas { position: relative; width: 1200px; height: 1000px; }
  .card {
    position: absolute; left: 269px; width: 662px; height: 378px; overflow: hidden;
  }
  .card-front {
    top: 108px;
    background: linear-gradient(120deg, var(--brand-blue) 0%, var(--brand-blue) 55%, var(--brand-blue-light) 100%);
  }
  .front-wordmark {
    position: absolute; right: 31px; top: 294px;
    color: var(--card-white); font-weight: 700; font-size: 40px;
    letter-spacing: 1px;
  }
  .card-back { top: 521px; background: var(--card-white); }
  .accent-bars { position: absolute; left: 0; top: 47px; }
  .holder-name {
    position: absolute; left: 38px; top: 46px;
    color: var(--brand-blue); font-weight: 500; font-size: 20px;
  }
  .holder-title {
    position: absolute; left: 38px; top: 71px;
    color: var(--text-grey); font-size: 14px;
  }
  .address {
    position: absolute; left: 38px; top: 244px;
    color: var(--text-grey); font-size: 15px; line-height: 21px; font-style: normal;
  }
  .contact-list {
    position: absolute; left: 38px; top: 302px; list-style: none;
    color: var(--text-grey); font-size: 15px; line-height: 21px;
  }
  .contact-list li { display: flex; align-items: center; gap: 5px; }
  .contact-list svg { fill: var(--brand-blue); }
  .back-wordmark {
    position: absolute; right: 38px; top: 190px;
    display: flex; align-items: center; gap: 10px;
    color: var(--brand-blue); font-weight: 700; font-size: 30px;
  }
  .wordmark-square { width: 18px; height: 18px; background: var(--brand-blue); }
  .footer-bands { position: absolute; left: 0; bottom: 0; }
  .website {
    position: absolute; right: 38px; bottom: 5px;
    color: var(--card-white); font-size: 14px;
  }
</style>
</head>
<body>
<main class="canvas">
  <section class="card card-front" aria-label="Card front">
    <div class="front-wordmark">Dunmore Roofing</div>
  </section>

  <section class="card card-back" aria-label="Card back">
    <svg class="accent-bars" width="16" height="34" viewBox="0 0 16 34" aria-hidden="true">
      <polygon points="0,0 6,0 2,34 0,34" fill="var(--brand-blue)"/>
      <polygon points="9,0 15,0 11,34 5,34" fill="var(--brand-grey)"/>
    </svg>
    <h1 class="holder-name">Paul Dunmore</h1>
    <p class="holder-title">Owner</p>

    <address class="address">4172 Township road 43<br>Ashcombe, WR K9X4T2</address>

    <ul class="contact-list">
      <li>
        <svg width="12" height="12" viewBox="0 0 24 24" aria-hidden="true"><path d="M6.6 10.8a15.1 15.1 0 0 0 6.6 6.6l2.2-2.2c.3-.3.7-.4 1-.2 1.1.4 2.3.6 3.6.6.6 0 1 .4 1 1V20c0 .6-.4 1-1 1A17 17 0 0 1 3 4c0-.6.4-1 1-1h3.5c.6 0 1 .4 1 1 0 1.3.2 2.5.6 3.6.1.3 0 .7-.2 1z"/></svg>
        (555) 204-0147
      </li>
      <li>
        <svg width="12" height="10" viewBox="0 0 24 18" aria-hidden="true"><path d="M0 0h24v18H0z M2 2l10 7 10-7" stroke="#fff" stroke-width="1.5"/></svg>
        paul@dunmoreroofing-example.com
      </li>
    </ul>

    <div class="back-wordmark"><span class="wordmark-square"></span>Dunmore Roofing</div>

    <svg class="footer-bands" width="662" height="28" viewBox="0 0 662 28" aria-hidden="true">
      <polygon points="0,17 370,17 360,28 0,28" fill="var(--brand-grey)"/>
      <polygon points="380,0 662,0 662,28 360,28" fill="var(--brand-blue)"/>
    </svg>
    <div class="website">www.dunmoreroofing-example.com</div>
  </section>
</main>
</body>
</html>
```